STAND OUT BUSINESS CARD REQUIRED

I would like a business card that is going to be different and stand out!

Target Market(s)

Residential market, adults from 28yrs on

Industry/Entity Type

Electrician

Requirements
Must have
• Business name
• my name
• phone number
• email
• web address
• license no.
• abn
• fax no
• logo
Nice to have
• Extra info:
• FREE quotes
• Fixed pricing
• On time guarantee
• Life time labour Guarantee

```html
<!DOCTYPE html>
<html lang="en">
<head>
<meta charset="utf-8">
<title>Bright Spark Wiring – Business Card</title>
<link rel="stylesheet" href="https://fonts.googleapis.com/css2?family=Oswald:wght@500&family=Quicksand:wght@500;700&display=swap">
<style>
  :root {
    --page-bg: #f2f2f2;
    --orange: #f7941d;
    --orange-deep: #e8720c;
    --yellow-glow: #ffd23a;
    --dome-center: #3b2b20;
    --dome-edge: #0e0b09;
    --ink: #1a1410;
    --white: #ffffff;
    --footer-ink: #2b2b2b;
    --green: #2fa84f;
  }
  * { box-sizing: border-box; margin: 0; padding: 0; }
  html, body {
    width: 1200px;
    height: 873px;
    overflow: hidden;
    background: var(--page-bg);
  }
  .canvas {
    position: relative;
    width: 1200px;
    height: 873px;
  }
  .business-card {
    position: absolute;
    left: 370px;
    top: 36px;
    width: 460px;
    height: 800px;
    overflow: hidden;
    background: radial-gradient(ellipse 70% 45% at 45% 22%, var(--yellow-glow) 0%, var(--orange) 55%, var(--orange-deep) 100%);
    box-shadow: 0 6px 22px rgba(0,0,0,0.22);
    font-family: "Quicksand", sans-serif;
  }
  .hero-illustration {
    position: absolute;
    left: 60px;
    top: 20px;
    width: 390px;
    height: 250px;
    border-radius: 30px;
    background: radial-gradient(ellipse at 40% 55%, rgba(60,150,70,0.45) 0%, rgba(200,60,30,0.25) 45%, rgba(255,255,255,0) 75%);
  }
  .dome {
    position: absolute;
    left: 0;
    top: 0;
    width: 460px;
    height: 800px;
  }
  .brand-name {
    position: absolute;
    left: 0;
    right: 0;
    top: 278px;
    text-align: center;
    font-family: "Oswald", sans-serif;
    font-weight: 500;
    font-size: 34px;
    line-height: 1;
    letter-spacing: 1px;
    color: var(--ink);
    text-transform: uppercase;
  }
  .name-banner {
    position: absolute;
    left: 0;
    top: 440px;
    width: 292px;
    height: 40px;
    background: var(--orange);
    clip-path: polygon(0 0, 90% 0, 100% 100%, 0 100%);
    display: flex;
    align-items: center;
    padding-left: 72px;
  }
  .name-banner .person-name {
    font-family: "Oswald", sans-serif;
    font-weight: 500;
    font-size: 26px;
    letter-spacing: 1px;
    color: var(--ink);
  }
  .contact-list {
    position: absolute;
    left: 72px;
    top: 502px;
    list-style: none;
    font-size: 21px;
    line-height: 31px;
    color: var(--white);
    font-weight: 500;
  }
  .contact-list .label {
    color: var(--orange);
    font-weight: 700;
  }
  .selling-points {
    position: absolute;
    left: 0;
    right: 0;
    top: 684px;
    height: 116px;
    background: var(--white);
    text-align: center;
    padding-top: 18px;
    color: var(--footer-ink);
    font-weight: 700;
    font-size: 17px;
    line-height: 32px;
  }
  .selling-points .free {
    color: var(--green);
    font-style: italic;
  }
</style>
</head>
<body>
<main class="canvas">
  <article class="business-card">
    <div class="hero-illustration" role="img" aria-label="Cartoon electrician superhero in green suit and red cape flying, with a hand holding up a light bulb"></div>

    <svg class="dome" viewBox="0 0 460 800" aria-hidden="true">
      <defs>
        <radialGradient id="domeShade" cx="0.5" cy="0.45" r="0.6">
          <stop offset="0" stop-color="var(--dome-center)"/>
          <stop offset="1" stop-color="var(--dome-edge)"/>
        </radialGradient>
      </defs>
      <path d="M0 432 Q230 238 460 432 L460 680 L0 680 Z" fill="url(#domeShade)"/>
      <rect x="0" y="678" width="460" height="6" fill="var(--orange)"/>
    </svg>

    <div class="brand-name">Bright Spark Wiring Pty Ltd</div>

    <div class="name-banner">
      <span class="person-name">JOHN DOE</span>
    </div>

    <ul class="contact-list">
      <li><span class="label">phone:</span> 000.000.0000</li>
      <li><span class="label">fax:</span> 000.000.0000</li>
      <li><span class="label">email:</span> johndoe@email.com</li>
      <li><span class="label">address:</span> 123 Anywhere</li>
    </ul>

    <footer class="selling-points">
      <p><span class="free">FREE</span> quotes | Fixed pricing</p>
      <p>On-time Guarantee | Lifetime labour Guarantee</p>
    </footer>
  </article>
</main>
</body>
</html>
```